Etiketten-Design für einen importierten Honig
Zielgruppe
Wir importieren originalen Manuka Honig aus Neuseeland. Der Manuka Honig ist bekannt für seine besonderen Eigenschaften (antibakteriell, etc.). Ein Glas unseres Honigs (500g) kostet zwischen 30 und 150 EUR.
Unsere Zielgruppe sind gesundheitsbewusste Kunden, die wenig preissensibel sind. Überwiegend wird der Manuka Honig im Fachhandel (z.B. Reformhaus, Drogerie, Biomarkt, etc.) verkauft. Der Großteil unserer Kunden ist 30+ Jahre.
Aufgabenstellung
Bei dem Etikett handelt es sich um das erste Produktetikett. Damit ist in der Farbgestaltung noch alles offen. Das Logo und der Name ist jedoch fix.
Das Etikett ist wird auf einem bpa-freien schwarzen Plastikbehälter angebracht. Dieser ist bei Manuka Honigen Standard aufgrund des langen Transports von Neuseeland nach Deutschland (gerne googeln). Der Deckel dieses Behälters ist schwarz.
Nachdem es sich um ein hochpreisiges Produkt handelt, soll das Etikett diese hohe Wertigkeit widerspiegeln. Damit ist eine Veredelung des Etiketts notwendig. Viele Konkurrenten arbeiten mit Gold, alternative Farben sind jedoch auch möglich.
Das Etikett überdeckt drei der vier Seiten des Plastikbehälters (vorne + links + rechts). Die Maße sind 160 mm x 60 mm. Zusätzlich zu den Etikettenmaßen bitte 2 mm Beschnittzugabe je Seite hinzufügen.
Hintergrundinformationen zu unserer Marke:
- Der Markenname lautet Kalvio. Der Markenname leitet sich von der ersten Imkerin Neuseelands ab - Edith Carrow. Sie hatte im Jahr 1839 die ersten Bienenstöcke nach Neuseeland gebracht und den ersten Manuka Honig geerntet.
- Unser Logo ist eine Verbindung einer Frau und den neuseeländischen Farn. Dieses Logo stellt also direkt eine Verbindung zu Neuseeland dar.
- Unsere Marke Kalvio ist eine qualitativ hochwertige, luxuriöse und hochpreisige Marke. Genau wie in dem Logo selbst, sollen diese Verbindungen zu Neuseeland, der Natur (Honig ist ein Naturprodukt) und Edith Carrow auch auf dem Etikett zu finden sein.
Wonach suchen wir:
- Wir sind auf der Suche nach einem einzigartigen Design, der unseren Honig besonders hervorhebt. Das Etikett soll auffällig sein und uns von anderen unterscheiden. (Eye-catching)
- Eine Veredelung des Etiketts ist Pflicht, da dies für uns die Wertigkeit des Etiketts und des Produktes stark erhöht. In welcher Art die Veredelung durchgeführt wird, ist Ihnen überlassen.
Das dürfen Sie frei wählen:
- Bisher haben..

```html
<!DOCTYPE html>
<html lang="de">
<head>
<meta charset="utf-8">
<title>Kalvio Manuka Honig – Etikett</title>
<link rel="stylesheet" href="https://fonts.googleapis.com/css2?family=Lato:wght@400;700&display=swap">
<style>
  :root {
    --page: #ffffff;
    --label: #2a2a2a;
    --ink: #f4f4f4;
    --ink-soft: #dcdcdc;
    --gold: #d9a92a;
    --gold-light: #f1cf55;
    --gold-deep: #b98a12;
    --ornament: #4a4a4a;
    --blank: #ffffff;
  }
  * { margin: 0; padding: 0; box-sizing: border-box; }
  html, body { width: 1200px; height: 732px; overflow: hidden; background: var(--page); }
  body { position: relative; font-family: "Lato", sans-serif; color: var(--ink); }

  .label {
    position: absolute; left: 120px; top: 240px;
    width: 965px; height: 359px;
    background: var(--label);
    overflow: hidden;
  }
  .abs { position: absolute; white-space: nowrap; }
  .center { text-align: center; }

  /* Side panel: nutrition */
  .nutrition-title { left: 54px; width: 200px; top: 40px; font-size: 10.5px; font-weight: 700; line-height: 14px; }
  .nutrition-table { left: 58px; top: 59px; width: 191px; border-collapse: collapse; font-size: 10.5px; }
  .nutrition-table td { height: 14px; padding: 0; line-height: 14px; white-space: nowrap; }
  .nutrition-table td:last-child { text-align: right; }
  .nutrition-table .sub td:first-child { padding-left: 7px; }
  .storage-note { left: 52px; width: 200px; top: 168px; font-size: 8px; line-height: 10.5px; }
  .infant-note { left: 52px; width: 200px; top: 199px; font-size: 8px; line-height: 10.5px; letter-spacing: .2px; }
  .blank-field { left: 41px; top: 260px; width: 225px; height: 99px; background: var(--blank); }

  /* Front panel */
  .ornament-area {
    left: 260px; top: 125px; width: 443px; height: 234px;
    background: radial-gradient(ellipse at 50% 45%, var(--ornament) 0%, rgba(74,74,74,.45) 55%, rgba(42,42,42,0) 75%);
    opacity: .55;
  }
  .brand-tile {
    left: 421px; top: 0; width: 121px; height: 140px;
    background: linear-gradient(135deg, var(--gold-light) 0%, var(--gold) 45%, var(--gold-deep) 100%);
  }
  .brand-name {
    position: absolute; left: 0; right: 0; top: 101px;
    font-size: 17px; line-height: 20px; font-weight: 400; letter-spacing: 1.2px; color: #ffffff; text-align: center;
  }
  .product-title { left: 282px; width: 400px; top: 208px; font-size: 33px; line-height: 40px; font-weight: 700; letter-spacing: .8px; color: #ffffff; }
  .product-grade { left: 282px; width: 400px; top: 246px; font-size: 33px; line-height: 40px; font-weight: 700; letter-spacing: .5px; color: var(--gold); }
  .product-origin { left: 282px; width: 400px; top: 285px; font-size: 19px; line-height: 24px; font-weight: 700; letter-spacing: .8px; color: #ffffff; }

  /* Side panel: story */
  .story-title { left: 633px; width: 300px; top: 16px; font-size: 18px; font-weight: 700; line-height: 23px; letter-spacing: .9px; color: var(--gold); }
  .story-text { left: 633px; width: 300px; font-size: 11.5px; font-weight: 700; line-height: 15.3px; letter-spacing: .45px; }
  .story-text.one { top: 75px; }
  .story-text.two { top: 151px; }
  .content-info { left: 633px; width: 300px; top: 238px; font-size: 10px; line-height: 12.5px; letter-spacing: .35px; color: var(--ink-soft); }
  .importer-info { left: 633px; width: 300px; top: 274px; font-size: 10px; line-height: 12.5px; letter-spacing: .35px; color: var(--ink-soft); }
  .net-weight { left: 633px; width: 300px; top: 324px; font-size: 18px; line-height: 22px; font-weight: 700; color: #ffffff; }
  .net-weight .estimate { font-weight: 400; margin-right: 4px; }
</style>
</head>
<body>
  <main class="label">
    <h2 class="abs nutrition-title center">Nährwertangaben pro 100 g</h2>
    <table class="abs nutrition-table">
      <tr><td>Energie</td><td>1400 kJ / 329 kcal</td></tr>
      <tr><td>Fett</td><td>0,8g</td></tr>
      <tr class="sub"><td>davon gesättigte Fettsäuren</td><td>0,5g</td></tr>
      <tr><td>Kohlenhydrate</td><td>80,4g</td></tr>
      <tr class="sub"><td>davon Zucker</td><td>65,4g</td></tr>
      <tr><td>Eiweiß</td><td>0,1g</td></tr>
      <tr><td>Salz</td><td>0,02g</td></tr>
    </table>
    <p class="abs storage-note center">1 Portion = 10g, Trocken, dunkel und<br>nicht über 25 °C lagern.</p>
    <p class="abs infant-note center">HONIG IST FÜR SÄUGLINGE UNTER<br>12 MONATEN NICHT GEEIGNET</p>
    <div class="abs blank-field"></div>

    <div class="abs ornament-area" role="img" aria-label="Dezentes Bienen-Ornament im Maori-Stil"></div>
    <div class="abs brand-tile">
      <span class="brand-name">KALVIO</span>
    </div>
    <h1 class="abs product-title center">MANUKA HONIG</h1>
    <p class="abs product-grade center">MGO 450+</p>
    <p class="abs product-origin center">AUS NEUSEELAND</p>

    <h2 class="abs story-title center">MANUKA HONIG –<br>DAS GOLD DER MAORI</h2>
    <p class="abs story-text one center">Bereits die Ureinwohner Neuseelands,<br>die Maori, wussten um die Kostbarkeit des<br>Manuka Honigs und nutzten ihn für seine<br>besonderen Eigenschaften.</p>
    <p class="abs story-text two center">Der Anteil des in diesem Honig enthaltenen<br>Wirkstoffs Methylglyoxal (MGO) wurde<br>durch ein akkreditiertes Labor auf mindes-<br>tens 450 mg/kg geprüft.</p>
    <p class="abs content-info center">Inhalt:<br>100 % Manuka Honig aus Neuseeland</p>
    <p class="abs importer-info center">Importiert und vertrieben durch:<br>Tawhiro GmbH, Lindenweg 12,<br>83421 Ambach</p>
    <p class="abs net-weight center"><span class="estimate">℮</span>500g</p>
  </main>
</body>
</html>
```